Business Card Design and Logo Needed

I need Business Cards and a Logo for my website and public speaking business which can be found at: www.corvina-lett.example

I'm looking for creative and unique ideas. Some business cards I've found online that I like can be found at:
http://gigbarrow.example/general/18-smokin-hot-business-card-designs/

and at

http://www.plumquarry.example/2009/04/50-creative-business-cards-of-50-graphic-designers/

```html
<!DOCTYPE html>
<html lang="en">
<head>
<meta charset="utf-8">
<title>Corvina Lett — Business Card</title>
<link rel="stylesheet" href="https://fonts.googleapis.com/css2?family=Oswald:wght@500;600&family=Sacramento&display=swap">
<style>
  :root {
    --card-tan: #ccad8e;
    --ornament-tone: #b8977a;
    --ornament-deep: #a6846a;
    --ink: #2a0e0b;
  }
  html, body {
    margin: 0;
    padding: 0;
    overflow: hidden;
    background: var(--card-tan);
  }
  .card {
    position: relative;
    width: 1200px;
    height: 667px;
    background: var(--card-tan);
    color: var(--ink);
    overflow: hidden;
  }
  .motto {
    position: absolute;
    z-index: 2;
    top: 40px;
    left: 446px;
    margin: 0;
    font-family: "Oswald", sans-serif;
    font-weight: 600;
    font-size: 19px;
    line-height: 1;
    letter-spacing: 13.4px;
    white-space: nowrap;
  }
  .monogram-area {
    position: absolute;
    z-index: 1;
    left: 6px;
    top: 17px;
    width: 430px;
    height: 650px;
  }
  .monogram-area svg {
    display: block;
    width: 100%;
    height: 100%;
  }
  .brand-mark {
    position: absolute;
    left: 0;
    top: 0;
    width: 400px;
    height: 650px;
    display: flex;
    flex-direction: column;
    align-items: center;
    justify-content: center;
    font-family: "Oswald", sans-serif;
    font-weight: 600;
    font-size: 52px;
    line-height: 1.05;
    letter-spacing: 6px;
    color: var(--ink);
  }
  .identity {
    position: absolute;
    z-index: 2;
    left: 500px;
    width: 600px;
    text-align: center;
    white-space: nowrap;
  }
  .name {
    top: 300px;
    margin: 0;
    font-family: "Sacramento", cursive;
    font-weight: 400;
    font-size: 104px;
    line-height: 1;
    letter-spacing: 2px;
  }
  .roles {
    top: 424px;
    margin: 0;
    font-family: "Oswald", sans-serif;
    font-weight: 600;
    font-size: 17px;
    line-height: 1.2;
    letter-spacing: 1.6px;
  }
  .site {
    top: 610px;
    margin: 0;
    font-family: "Oswald", sans-serif;
    font-weight: 600;
    font-size: 22px;
    line-height: 1.2;
    letter-spacing: 2.6px;
  }
</style>
</head>
<body>
  <main class="card">
    <p class="motto">WONDER. EXPLORE. DREAM. ACHIEVE.</p>

    <div class="monogram-area">
      <svg viewBox="0 0 430 650" role="img" aria-label="Ornamental swirling flourishes framing the brand mark">
        <defs>
          <radialGradient id="ornament-glow" cx="50%" cy="50%" r="55%">
            <stop offset="0%" stop-color="var(--ornament-deep)"/>
            <stop offset="70%" stop-color="var(--ornament-tone)"/>
            <stop offset="100%" stop-color="var(--card-tan)"/>
          </radialGradient>
        </defs>
        <rect x="0" y="0" width="430" height="650" rx="40" fill="url(#ornament-glow)"/>
      </svg>
      <div class="brand-mark">
        <span>CORVINA</span>
        <span>LETT</span>
      </div>
    </div>

    <h1 class="identity name">Corvina Lett</h1>
    <p class="identity roles">SPEAKER, PHILANTHROPIST, AUTHOR</p>
    <p class="identity site">HTTP://WWW.CORVINA-LETT.EXAMPLE</p>
  </main>
</body>
</html>
```